KTWG application splash screen

We need a 1024x768 image for use as an application splash screen.
The image will be displayed full screen on an 10 inch industrial PC 1024x768 screen while our application is launching. The image should convey that the application is "Waiting for connection to Wi-Fi access point..." and include a graphic of the industrial PC connected to the access point via an Ethernet cable. A list of troubleshooting steps should be included at the bottom of the image. The troubleshooting steps should not be the main focus of the image and should be shown in a smaller font (but still readable at 1024x768 displayed on a 10 inch screen).
I will include a mock up of the general idea of what we are looking for as well as image files for the industrial PC, a screenshot of our application to show on the PC's screen and the AP.
For general look and feel and a sense of corporate branding please review our website https://marrowgatesoilworks.example/. The splash screen should reflect corporate branding.
Target Market(s)
Users of our application
Industry/Entity Type
Agriculture
Look and feel

```html
<!DOCTYPE html>
<html lang="en">
<head>
<meta charset="utf-8">
<title>KTWG – Waiting for connection</title>
<link href="https://fonts.googleapis.com/css2?family=Archivo+Black&family=Poppins:wght@400;500;600&display=swap" rel="stylesheet">
<style>
  :root {
    --page-bg: #999999;
    --card-bg: #ffffff;
    --brand-green: #43bf6a;
    --deep-green: #1f7a3c;
    --ink: #0d0d0d;
    --muted-ink: #222222;
    --dash: #c8c8c8;
    --signal-red: #e8322b;
    --device-dark: #2a2a2a;
    --device-light: #eceff0;
  }
  * { box-sizing: border-box; margin: 0; padding: 0; }
  html, body { width: 1200px; height: 1200px; overflow: hidden; background: var(--page-bg); }
  body { position: relative; font-family: "Poppins", sans-serif; }

  .splash {
    position: absolute; left: 0; top: 150px;
    width: 1200px; height: 900px;
    background: var(--card-bg);
    overflow: hidden;
  }
  .abs { position: absolute; }

  .brand { left: 79px; top: 80px; display: flex; align-items: center; gap: 12px; }
  .brand-dot { width: 28px; height: 28px; border-radius: 50%; background: var(--brand-green); }
  .brand-name { font-weight: 600; font-size: 56px; line-height: 1; color: var(--ink); letter-spacing: 1px; }

  .headline { left: 324px; top: 50px; font-family: "Archivo Black", sans-serif; text-transform: uppercase; line-height: 1; white-space: nowrap; font-weight: 400; }
  .headline-main { display: block; font-size: 49px; color: var(--ink); }
  .headline-sub { display: block; font-size: 49px; color: var(--brand-green); margin-top: 15px; }

  .device-label { font-weight: 500; font-size: 23px; line-height: 32px; color: var(--ink); }
  .device-label--pc { right: 990px; top: 274px; text-align: right; }
  .device-label--ap { left: 988px; top: 274px; }
  .device-model { left: 988px; top: 381px; font-size: 13px; line-height: 17px; color: var(--muted-ink); }

  .cab-computer { left: 243px; top: 242px; width: 231px; height: 184px; border-radius: 12px;
    background: linear-gradient(180deg, var(--device-dark), #111); }
  .access-point { left: 947px; top: 251px; width: 22px; height: 162px; border-radius: 6px;
    background: linear-gradient(90deg, #d9dcdd, var(--device-light), #d0d3d4); }

  .warning { left: 566px; top: 214px; }
  .wifi-icon { left: 1006px; top: 260px; }
  .cable-label { left: 578px; top: 410px; width: 200px; text-align: center; font-weight: 500; font-size: 23px; color: var(--ink); }
  .cable-line { left: 0; top: 0; }

  .help-title { left: 0; top: 495px; width: 1200px; text-align: center; font-family: "Archivo Black", sans-serif; font-weight: 400; font-size: 34px; color: var(--brand-green); letter-spacing: 0.5px; }
  .help-note { left: 0; top: 543px; width: 1200px; text-align: center; font-size: 16px; color: var(--ink); }

  .help-band { left: 0; top: 587px; width: 1200px; height: 313px; background: var(--brand-green); color: #fff; }
  .help-lead { position: absolute; left: 0; top: 20px; width: 1200px; text-align: center; font-weight: 600; font-size: 22px; }
  .step-list { position: absolute; list-style: none; }
  .step-list--left { left: 107px; top: 90px; width: 420px; }
  .step-list--right { left: 708px; top: 90px; width: 370px; }
  .step { position: relative; padding-left: 21px; font-size: 16.5px; line-height: 21px; }
  .step-list--left .step { margin-bottom: 29px; }
  .step-list--right .step { margin-bottom: 50px; }
  .step::before { content: ""; position: absolute; left: 0; top: 4px; width: 13px; height: 13px; border-radius: 50%; background: var(--deep-green); }
  .step::after { content: ""; position: absolute; left: 4px; top: 7px; width: 5px; height: 3px;
    border-left: 1.5px solid var(--brand-green); border-bottom: 1.5px solid var(--brand-green); transform: rotate(-45deg); }
  .tools-mark { left: 556px; top: 93px; width: 128px; height: 128px; border-radius: 50%;
    border: 10px solid rgba(31, 122, 60, 0.55); }
</style>
</head>
<body>
<main class="splash">
  <div class="abs brand">
    <span class="brand-dot"></span>
    <span class="brand-name">KTWG</span>
  </div>

  <h1 class="abs headline">
    <span class="headline-main">Waiting for connection</span>
    <span class="headline-sub">To Wi–Fi access point…</span>
  </h1>

  <p class="abs device-label device-label--pc">Tractor<br>cab<br>computer</p>
  <div class="abs cab-computer" role="img" aria-label="Photo of the rugged tractor cab computer showing the seeding application"></div>

  <svg class="abs warning" width="222" height="180" viewBox="0 0 222 180" aria-hidden="true">
    <polygon points="111,0 222,180 0,180" fill="var(--brand-green)"/>
    <rect x="97" y="54" width="28" height="70" fill="#fff"/>
    <rect x="97" y="138" width="28" height="24" fill="#fff"/>
  </svg>

  <p class="abs cable-label">Ethernet cable</p>
  <svg class="abs cable-line" width="1200" height="460" aria-hidden="true">
    <polyline points="358,431 358,453 958,453 958,421" fill="none" stroke="var(--dash)" stroke-width="4" stroke-dasharray="9 7"/>
  </svg>

  <div class="abs access-point" role="img" aria-label="Photo of the outdoor Wi-Fi access point with two antennas"></div>
  <svg class="abs wifi-icon" width="22" height="17" viewBox="0 0 24 18" aria-hidden="true">
    <path d="M2 7a14 14 0 0 1 20 0" fill="none" stroke="var(--signal-red)" stroke-width="2"/>
    <path d="M6 11a8.5 8.5 0 0 1 12 0" fill="none" stroke="var(--signal-red)" stroke-width="2"/>
    <circle cx="12" cy="15" r="2" fill="var(--signal-red)"/>
  </svg>
  <p class="abs device-label device-label--ap">Wi–Fi<br>Access<br>Point</p>
  <p class="abs device-model">Northbeam<br>NB-220 Outdoor</p>

  <h2 class="abs help-title">Troubleshooting steps</h2>
  <p class="abs help-note">This screen should only be visible for a short time on boot</p>

  <section class="abs help-band">
    <p class="help-lead">If this screen stays visible for more than a</p>
    <ul class="step-list step-list--left">
      <li class="step">Verify that the Wi-Fi Access Point (AP) powers up when this system does (indicated by a green light on the side of the AP).</li>
      <li class="step">Check the Ethernet cable between this system and the AP for damage, and replace it if necessary.</li>
    </ul>
    <div class="abs tools-mark" role="img" aria-label="Gear and wrench service icon"></div>
    <ul class="step-list step-list--right">
      <li class="step">Power-cycle this system and wait for it to reboot fully.</li>
      <li class="step">If the issue persists, contact KTWG support for further assistance.</li>
    </ul>
  </section>
</main>
</body>
</html>
```